Breakfast Cafe - The Sunny Nook

It is for my breakfast and lunch cafe with a hawaiian / beach theme. I am open 7 days a week from 7am to 2pm. We serve traditional American food such as omelettes, pancakes, burgers and sandwiches. I'll upload my old card and my new logo to be used. We have a lot of day to day regulars who eat there during the week, our t-shirts actually say 'Locals Only' on them. Hope this helps. Thanks.

Target Market(s)

anyone who has an appetite!

Industry/Entity Type

American Restaurant

Contact Information for Business Card

4815C Marlow Grove Avenue
Long Beach, California
(555) 731-2294

Requirements
Must have
• Address and phone number easily readable.
Nice to have
• beach or tropical theme

```html
<!DOCTYPE html>
<html lang="en">
<head>
<meta charset="utf-8">
<title>The Sunny Nook – Business Card</title>
<link rel="stylesheet" href="https://fonts.googleapis.com/css2?family=Bebas+Neue&family=Oswald:wght@500&display=swap">
<style>
  :root {
    --page: #e6e6e4;
    --sky: #5bbfd8;
    --sand: #d9a876;
    --sand-light: #ecd9ad;
    --foam: #ffffff;
    --ink: #161616;
    --rule: #2a2a2a;
    --sun: #f4a93a;
    --name: #6b3d16;
    --palm-leaf: #1f9a5a;
    --palm-trunk: #a8621f;
  }
  * { margin: 0; padding: 0; box-sizing: border-box; }
  html, body { width: 1200px; height: 960px; overflow: hidden; background: var(--page); }
  .card {
    position: absolute; left: 77px; top: 182px;
    width: 1046px; height: 596px;
    overflow: hidden;
    font-family: "Bebas Neue", "Oswald", sans-serif;
    color: var(--ink);
  }
  .card-scene { position: absolute; inset: 0; }
  .brand {
    position: absolute; left: 40px; top: 40px; width: 400px;
    display: flex; flex-direction: column; align-items: center;
  }
  .brand-mark {
    width: 330px; height: 330px; border-radius: 50%;
    background: var(--sun);
  }
  .brand-name {
    margin-top: 10px;
    font-size: 66px; line-height: 1; letter-spacing: 1px;
    color: var(--name);
    white-space: nowrap;
  }
  .tagline {
    position: absolute; left: 600px; top: 150px; width: 380px;
    text-align: center;
  }
  .tagline-title { font-size: 58px; line-height: 0.92; letter-spacing: 1px; }
  .tagline-hours {
    font-family: "Oswald", sans-serif; font-weight: 500;
    font-size: 24px; line-height: 1.3; margin-top: 10px;
  }
  .tagline-hours .days {
    display: inline-block; padding: 0 4px 3px;
    border-bottom: 2px solid var(--rule);
  }
  .phone {
    position: absolute; left: 40px; top: 497px; width: 400px;
    text-align: center; font-size: 64px; line-height: 1; letter-spacing: 1px;
  }
  .address {
    position: absolute; left: 560px; top: 475px; width: 440px;
    text-align: center; font-size: 34px; line-height: 1.1; letter-spacing: 0.5px;
  }
</style>
</head>
<body>
  <main class="card">
    <svg class="card-scene" width="1046" height="596" viewBox="0 0 1046 596" aria-hidden="false">
      <defs>
        <linearGradient id="palm-tone" x1="0" y1="0" x2="1" y2="1">
          <stop offset="0" stop-color="var(--palm-leaf)"/>
          <stop offset="0.6" stop-color="var(--palm-leaf)"/>
          <stop offset="1" stop-color="var(--palm-trunk)"/>
        </linearGradient>
      </defs>
      <rect class="sky" width="1046" height="596" fill="var(--sky)"/>
      <path class="sand-light" d="M0 382 C 180 350, 300 350, 470 372 C 680 400, 880 410, 1046 400 L1046 596 L0 596 Z" fill="var(--sand-light)"/>
      <path class="foam" d="M0 365 C 180 335, 300 335, 470 352 C 680 376, 880 385, 1046 380 L1046 400 C 880 410, 680 400, 470 372 C 300 350, 180 350, 0 382 Z" fill="var(--foam)"/>
      <path class="sand" d="M0 395 C 180 365, 300 368, 470 390 C 680 418, 880 430, 1046 425 L1046 596 L0 596 Z" fill="var(--sand)"/>
      <path class="palm" role="img" aria-label="Palm tree leaning in from the top right corner"
            d="M740 0 L1046 0 L1046 330 L1020 330 C 1010 250, 980 170, 930 120 C 880 80, 800 70, 740 60 Z"
            fill="url(#palm-tone)"/>
    </svg>

    <section class="brand">
      <div class="brand-mark"></div>
      <h1 class="brand-name">The Sunny Nook</h1>
    </section>

    <section class="tagline">
      <h2 class="tagline-title">Breakfast &amp;<br>Lunch Cafe</h2>
      <p class="tagline-hours"><span class="days">OPEN 7 DAYS A WEEK FROM</span><br>7AM TO 2PM.</p>
    </section>

    <p class="phone">(555) 731-2294</p>
    <p class="address">4815C Marlow Grove<br>Avenue Long Beach, California</p>
  </main>
</body>
</html>
```